BRAVE MOTION Personal Training Website.

I am looking for a website design for Word Press URL I already have. I have it as 10 very simple pages. Once home page design is set we can use that look on all other pages. I have uploaded a word document that has an outline of what I am looking for. Please take the time to review this. I want to add this is for a WordPress site.

Target Market(s)

Women 25-55

Industry/Entity Type

Health And Wellness

Coding

Coded - Design and coding required

Number of Pages Required

5+ page

```html
<!DOCTYPE html>
<html lang="en">
<head>
<meta charset="utf-8">
<title>BRAVE MOTION – Personal Training</title>
<link href="https://fonts.googleapis.com/css2?family=Poppins:wght@300;400;500;600;700&display=swap" rel="stylesheet">
<style>
:root{
  --red:#e2312a;
  --red-deep:#b81f1a;
  --ink:#222222;
  --dark:#1e1e1e;
  --dark-2:#2b2b2b;
  --grey:#6b6b6b;
  --light:#f2f2f2;
  --white:#ffffff;
}
*{box-sizing:border-box;margin:0;padding:0}
html,body{width:1200px;height:5389px;overflow:hidden}
body{font-family:"Poppins",Arial,sans-serif;color:var(--ink);background:var(--white);position:relative}
.abs{position:absolute}
section,header,footer{position:absolute;left:0;width:1200px;overflow:hidden}
.photo{position:absolute}
.red{color:var(--red)}
.sec-title{position:absolute;left:0;width:100%;text-align:center;font-size:27px;font-weight:600;color:var(--red)}
.play{position:absolute;width:64px;height:64px;border-radius:50%;background:var(--red);box-shadow:0 0 0 10px rgba(226,49,42,.35)}
.play::after{content:"";position:absolute;left:26px;top:20px;border-left:18px solid #fff;border-top:12px solid transparent;border-bottom:12px solid transparent}

/* hero */
.hero{top:0;height:700px;background:linear-gradient(110deg,#5a4a48 0%,#3a3030 35%,#2a2424 60%,#151313 100%)}
.hero-stripe{position:absolute;top:0;left:0}
.topbar{position:absolute;top:0;left:0;width:1200px;height:40px;background:rgba(0,0,0,.55)}
.nav{position:absolute;top:11px;font-size:13px;color:#fff;display:flex;gap:26px}
.nav-left{left:108px}
.nav-right{left:408px;gap:24px}
.brand{position:absolute;left:520px;top:52px;display:flex;align-items:center;gap:10px}
.brand-dot{width:46px;height:46px;border-radius:50%;background:var(--red)}
.brand-name{font-size:22px;font-weight:700;color:#fff;letter-spacing:.5px}
.call{position:absolute;right:62px;top:76px;display:flex;align-items:center;gap:12px;color:#fff;font-size:17px}
.call-icon{width:38px;height:38px;border-radius:50%;background:var(--red);display:flex;align-items:center;justify-content:center}
.call-num{color:var(--red);font-weight:500}
.social{position:absolute;left:62px;top:165px;display:flex;gap:14px}
.social span{width:14px;height:14px;border-radius:50%;background:rgba(255,255,255,.7)}
.tagline{position:absolute;left:698px;top:340px;color:#fff;font-size:33px;font-weight:600;line-height:1.3}

/* welcome */
.welcome{top:700px;height:486px}
.welcome h2{position:absolute;left:79px;top:62px;font-size:27px;font-weight:600}
.welcome .lead{position:absolute;left:79px;top:120px;width:590px;font-size:15px;font-weight:500;line-height:1.6}
.welcome .body{position:absolute;left:79px;top:200px;width:590px;font-size:13px;color:var(--grey);line-height:1.75}
.btn-red{position:absolute;background:var(--red);color:#fff;font-size:14px;font-weight:500;text-align:center}
.welcome .btn-red{left:79px;top:362px;width:130px;height:42px;line-height:42px}

/* ask */
.ask{top:1186px;height:190px;background:linear-gradient(90deg,var(--red-deep),var(--red) 45%,var(--red-deep))}
.ask-burst{position:absolute;left:30px;top:0;width:190px;height:150px;border-radius:50%;background:rgba(255,255,255,.12)}
.ask h3{position:absolute;left:0;width:100%;top:34px;text-align:center;color:#fff;font-size:28px;font-weight:600}
.field{position:absolute;border-bottom:1px solid rgba(255,255,255,.75);color:#fff;font-size:14px;padding-bottom:10px}
.ask .btn-white{position:absolute;left:862px;top:94px;width:194px;height:48px;background:#fff;color:var(--ink);font-size:15px;font-weight:600;text-align:center;line-height:48px}

/* certifications */
.certs{top:1400px;height:407px;background:var(--dark-2)}
.certs h2{position:absolute;left:259px;top:62px;font-size:27px;font-weight:600;color:var(--red)}
.certs p{position:absolute;left:259px;top:128px;width:760px;color:#fff;font-size:14px;line-height:1.75}
.cert{position:absolute;top:206px;width:165px;height:144px;background:#f7f7f7;border:6px solid #fff}
.cert::before{content:"";position:absolute;left:18px;right:18px;top:20px;height:8px;background:#d5d5d5;box-shadow:0 18px 0 #e4e4e4,0 36px 0 #e4e4e4,0 54px 0 #e4e4e4}
.cert::after{content:"";position:absolute;left:14px;bottom:12px;width:42px;height:16px;background:#b9c4d3}

/* videos */
.videos{top:1807px;height:870px;background:var(--dark)}
.videos .sec-title{top:50px}
.videos .intro{position:absolute;left:270px;width:660px;top:115px;text-align:center;color:#fff;font-size:14px;line-height:1.75}
.videos .side{position:absolute;left:79px;top:582px;width:300px;color:#fff;font-size:14px;line-height:1.7}
.btn-outline{position:absolute;left:79px;top:654px;width:190px;height:44px;border:2px solid #fff;border-radius:22px;color:#fff;font-size:16px;font-weight:600;text-align:center;line-height:40px}

/* online training */
.training{top:2677px;height:557px}
.training .sec-title{top:200px}
.card{position:absolute;top:269px;width:244px;height:210px;box-shadow:0 3px 10px rgba(0,0,0,.12)}
.card .photo{left:0;top:0;width:244px;height:170px}
.card .label{position:absolute;left:0;bottom:0;width:244px;height:44px;background:var(--red);color:#fff;font-size:15px;font-weight:500;text-align:center;line-height:44px}

/* testimonial */
.testi{top:3234px;height:503px;background:linear-gradient(90deg,#1a1a1a,#2e2a2a 50%,#1a1a1a)}
.testi h2{position:absolute;left:0;width:100%;top:52px;text-align:center;color:#fff;font-size:27px;font-weight:600}
.testi-frame{position:absolute;left:205px;top:138px;width:837px;height:248px;border:2px solid #d8d8d8}
.quote-box{position:absolute;left:568px;top:105px;width:64px;height:64px;background:#fff;display:flex;align-items:center;justify-content:center;font-size:58px;font-weight:700;color:var(--red);line-height:1;padding-top:22px}
.testi p{position:absolute;left:250px;width:750px;top:198px;text-align:center;color:#fff;font-size:14px;line-height:1.8}
.arrow{position:absolute;top:252px;width:30px;height:40px;background:#fff;display:flex;align-items:center;justify-content:center}
.avatar{position:absolute;top:362px;width:84px;height:84px;border-radius:50%;background:linear-gradient(160deg,#b9b2ae,#6f6461);border:4px solid #fff}
.avatar.active{border-color:var(--red);box-shadow:0 0 0 3px #fff}

/* blog */
.blog{top:3737px;height:485px}
.blog .sec-title{top:56px}
.post{position:absolute;top:133px;width:300px}
.post .photo{position:relative;width:300px;height:216px}
.post h4{margin-top:18px;font-size:17px;font-weight:600}
.post .meta{margin-top:6px;display:flex;justify-content:space-between;font-size:13px;color:var(--grey);border-bottom:1px solid #ddd;padding-bottom:8px}
.post .meta .more{color:var(--red);font-weight:500}

/* contact */
.contact{top:4222px;height:503px;background:linear-gradient(90deg,#d62a24,#e8463c 50%,#d62a24)}
.contact h2{position:absolute;left:0;width:100%;top:56px;text-align:center;color:#fff;font-size:27px;font-weight:600}
.contact .intro{position:absolute;left:260px;width:680px;top:118px;text-align:center;color:#fff;font-size:14px;line-height:1.7}
.contact .btn-white{position:absolute;left:550px;top:402px;width:133px;height:38px;background:#fff;color:var(--ink);font-size:15px;font-weight:600;text-align:center;line-height:38px}

/* subscribe */
.subscribe{top:4725px;height:305px}
.subscribe .sec-title{top:52px}
.subscribe .intro{position:absolute;left:0;width:100%;top:113px;text-align:center;color:var(--grey);font-size:13px}
.sub-field{position:absolute;top:193px;border-bottom:1px solid var(--red);color:var(--grey);font-size:14px;padding:0 0 10px 4px}
.subscribe .btn-red{left:895px;top:180px;width:129px;height:42px;line-height:42px}

/* footer */
.footer{top:5030px;height:359px;background:var(--dark)}
.footer h5{position:absolute;top:48px;color:var(--red);font-size:16px;font-weight:600}
.footer ul{position:absolute;top:84px;list-style:none;color:#fff;font-size:14px;line-height:32px}
.touch{position:absolute;left:449px;display:flex;align-items:flex-start;gap:14px;color:#fff;font-size:14px;line-height:1.6}
.touch svg{flex:none;margin-top:2px}
.foot-brand{position:absolute;left:918px;top:42px;display:flex;align-items:center;gap:8px}
.foot-brand .brand-dot{width:36px;height:36px}
.foot-brand .brand-name{font-size:17px}
.footer .about{position:absolute;left:826px;top:118px;width:342px;text-align:center;color:#fff;font-size:14px;line-height:1.7}
.footer .rule{position:absolute;left:79px;top:295px;width:1042px;height:1px;background:var(--red)}
.footer .copy{position:absolute;left:0;width:100%;top:312px;text-align:center;color:var(--red);font-size:14px}
</style>
</head>
<body>

<header class="hero">
  <div class="photo" role="img" aria-label="Photo of a woman running in a gym with a cap and sports top" style="left:0;top:0;width:1200px;height:700px;background:linear-gradient(100deg,rgba(160,120,120,.35),rgba(40,30,30,.1) 45%,rgba(0,0,0,.5))"></div>
  <svg class="hero-stripe" width="1200" height="700" viewBox="0 0 1200 700" aria-hidden="true">
    <polygon points="400,0 470,0 330,700 260,700" fill="#e2312a" opacity=".85"/>
    <polygon points="500,0 520,0 380,700 360,700" fill="#e2312a" opacity=".6"/>
  </svg>
  <div class="topbar"></div>
  <nav class="nav nav-left"><span>Certifications</span><span>Bio</span><span>Blog</span></nav>
  <nav class="nav nav-right"><span>Online Training</span><span>Functional Movement Screening</span><span>Nutrition Section</span><span>Merchandise</span><span>Contact Us</span></nav>
  <div class="brand"><span class="brand-dot"></span><span class="brand-name">BRAVE MOTION</span></div>
  <div class="call">Call on
    <span class="call-icon"><svg width="18" height="18" viewBox="0 0 24 24"><path fill="#fff" d="M6.6 10.8a15.1 15.1 0 0 0 6.6 6.6l2.2-2.2a1 1 0 0 1 1-.25 11.4 11.4 0 0 0 3.6.57 1 1 0 0 1 1 1V20a1 1 0 0 1-1 1A17 17 0 0 1 3 4a1 1 0 0 1 1-1h3.5a1 1 0 0 1 1 1c0 1.25.2 2.45.57 3.57a1 1 0 0 1-.25 1z"/></svg></span>
    <span class="call-num">123 456 7890</span></div>
  <div class="social"><span></span><span></span></div>
  <div class="tagline">If it doesn't Challenge you,<br>it won't Change you.</div>
</header>

<section class="welcome">
  <h2>Welcome To <span class="red">Brave Motion</span></h2>
  <p class="lead">Lorem Ipsum is simply dummy text of the printing and typesetting industry. Lorem Ipsum has been the industry's standard dummy text ever since the 1500s.</p>
  <p class="body">Lorem Ipsum is simply dummy text of the printing and typesetting industry. Lorem Ipsum has been the industry's standard dummy text ever since the 1500s, when an unknown printer took a galley of type and scrambled it to make a type electronic typesetting, remaining essentially unchanged.</p>
  <div class="btn-red">Learn More</div>
  <div class="photo" role="img" aria-label="Photo of a man and a woman doing kettlebell squats in a gym" style="left:726px;top:62px;width:323px;height:345px;background:linear-gradient(180deg,#8d8b88,#4f4c4a 60%,#3a3836)"></div>
  <div class="play" style="left:722px;top:202px;width:48px;height:48px"></div>
</section>

<section class="ask">
  <div class="ask-burst"></div>
  <h3>Ask Rae</h3>
  <div class="field" style="left:198px;top:104px;width:302px">Enter name</div>
  <div class="field" style="left:532px;top:104px;width:294px">Ask Training Question</div>
  <div class="btn-white">ASK QUESTION</div>
</section>

<section class="certs">
  <div class="photo" role="img" aria-label="Photo of a woman training with boxing gloves" style="left:0;top:0;width:234px;height:407px;background:linear-gradient(180deg,#6d6866,#3d3938)"></div>
  <h2>Certifications</h2>
  <p>Lorem Ipsum is simply dummy text of the printing and typesetting industry. Lorem Ipsum has been the industry's standard dummy text ever since the 1500s,</p>
  <div class="cert" style="left:252px"></div>
  <div class="cert" style="left:432px"></div>
  <div class="cert" style="left:612px"></div>
  <div class="cert" style="left:792px"></div>
  <div class="cert" style="left:972px"></div>
</section>

<section class="videos">
  <h2 class="sec-title">VIDEOS</h2>
  <p class="intro">Lorem Ipsum is simply dummy text of the printing and typesetting industry. Lorem Ipsum has been the industry's standard dummy text ever since the 1500s, when an unknown printer took a galley.</p>
  <div class="photo" role="img" aria-label="Video still of a woman training with dumbbells beside her coach" style="left:79px;top:216px;width:632px;height:302px;background:linear-gradient(120deg,#c9c3be,#8f8984)"></div>
  <div class="play" style="left:616px;top:262px"></div>
  <div class="photo" role="img" aria-label="Video still of a woman lifting dumbbells overhead" style="left:844px;top:266px;width:313px;height:431px;background:linear-gradient(180deg,#9a8f89,#5c5350)"></div>
  <div class="play" style="left:794px;top:450px;width:84px;height:84px"></div>
  <p class="side">Lorem Ipsum is simply dummy text of the printing and typesetting industry.</p>
  <div class="btn-outline">VIEW MORE</div>
  <div class="photo" role="img" aria-label="Video still of a woman stretching outdoors on grass" style="left:456px;top:582px;width:324px;height:316px;background:linear-gradient(180deg,#6f8f5a,#3f5a34)"></div>
  <div class="play" style="left:586px;top:758px"></div>
</section>

<section class="training">
  <h2 class="sec-title">Online Training</h2>
  <div class="card" style="left:79px"><div class="photo" role="img" aria-label="Illustration of a checklist with ticks and a pen" style="background:linear-gradient(135deg,#ffffff,#ececec)"></div><div class="label">Assessment</div></div>
  <div class="card" style="left:359px"><div class="photo" role="img" aria-label="Graphic for an eight week custom fat loss program" style="background:linear-gradient(135deg,#2c2c2c,#111)"></div><div class="label">Personalized Program</div></div>
  <div class="card" style="left:636px"><div class="photo" role="img" aria-label="Photo of fresh vegetables and healthy food" style="background:linear-gradient(135deg,#a4632f,#5b7a2c)"></div><div class="label">Nutrition</div></div>
  <div class="card" style="left:916px"><div class="photo" role="img" aria-label="Illustration of a figure giving support" style="background:linear-gradient(135deg,#ffffff,#ededed)"></div><div class="label">Support</div></div>
</section>

<section class="testi">
  <div class="photo" role="img" aria-label="Dim photo of a group fitness class" style="left:0;top:0;width:1200px;height:503px;background:linear-gradient(90deg,rgba(0,0,0,.2),rgba(90,80,80,.25),rgba(0,0,0,.2))"></div>
  <h2><span class="red">Client</span> Testimonial</h2>
  <div class="testi-frame"></div>
  <div class="quote-box">&ldquo;</div>
  <p>I wasn't sure if Raelyn was interested in training my then 15-year-old daughter. But after talking with her she was 100% committed to what we wanted to accomplish with our daughter. After their first intro session together, my daughter was excited and nervous about this new journey of training. However, it didn't take long for her to fall in love with her training sessions and Raelyn...</p>
  <div class="arrow" style="left:172px"><svg width="10" height="14" viewBox="0 0 10 14"><path d="M8 1 2 7l6 6" fill="none" stroke="#222" stroke-width="2"/></svg></div>
  <div class="arrow" style="left:1027px"><svg width="10" height="14" viewBox="0 0 10 14"><path d="m2 1 6 6-6 6" fill="none" stroke="#222" stroke-width="2"/></svg></div>
  <div class="avatar" role="img" aria-label="Client portrait" style="left:515px"></div>
  <div class="avatar active" role="img" aria-label="Client portrait" style="left:623px"></div>
</section>

<section class="blog">
  <h2 class="sec-title">Latest Blog</h2>
  <article class="post" style="left:79px"><div class="photo" role="img" aria-label="Photo of a woman on an elliptical trainer" style="background:linear-gradient(135deg,#e8e8e8,#9a9a9a)"></div><h4>Lorem Ipsum is typesetting industry.</h4><div class="meta"><span>Comments</span><span class="more">Learn More &rarr;</span></div></article>
  <article class="post" style="left:449px"><div class="photo" role="img" aria-label="Photo of people on exercise bikes" style="background:linear-gradient(135deg,#3d6e92,#1d2f40)"></div><h4>Lorem Ipsum is typesetting industry.</h4><div class="meta"><span>Comments</span><span class="more">Learn More &rarr;</span></div></article>
  <article class="post" style="left:823px"><div class="photo" role="img" aria-label="Photo of a couple training with dumbbells" style="background:linear-gradient(135deg,#3b5ea8,#7a5e50)"></div><h4>Lorem Ipsum is typesetting industry.</h4><div class="meta"><span>Comments</span><span class="more">Learn More &rarr;</span></div></article>
</section>

<section class="contact">
  <div class="photo" role="img" aria-label="Red tinted photo of a woman exercising" style="left:0;top:0;width:1200px;height:503px;background:linear-gradient(90deg,rgba(120,0,0,.15),rgba(255,255,255,.06),rgba(120,0,0,.15))"></div>
  <h2>Contact Us</h2>
  <p class="intro">Lorem Ipsum is simply dummy text of the printing and typesetting industry. Lorem Ipsum has been the industry's standard dummy text ever since the 1500s.</p>
  <div class="field" style="left:316px;top:222px;width:277px">Name*</div>
  <div class="field" style="left:647px;top:222px;width:280px">E-mail*</div>
  <div class="field" style="left:316px;top:276px;width:277px">Phone*</div>
  <div class="field" style="left:647px;top:276px;width:280px">Subject</div>
  <div class="field" style="left:316px;top:330px;width:611px;padding-bottom:36px">Message</div>
  <div class="btn-white">Submit</div>
</section>

<section class="subscribe">
  <h2 class="sec-title">Subscribe Us!</h2>
  <p class="intro">For latest news or updates subscribe our newsletter</p>
  <div class="sub-field" style="left:216px;width:341px">Name*</div>
  <div class="sub-field" style="left:568px;width:312px">E-mail*</div>
  <div class="btn-red">Subscribe</div>
</section>

<footer class="footer">
  <h5 style="left:79px">Site Map</h5>
  <ul style="left:79px"><li>Certifications</li><li>Bio</li><li>Blog</li><li>Videos</li><li>Online Training</li><li>Functional Movement Screening</li></ul>
  <ul style="left:270px"><li>Nutrition Section</li><li>Merchandise</li><li>Contact Us</li></ul>
  <h5 style="left:449px">Get In Touch</h5>
  <div class="touch" style="top:84px"><svg width="14" height="18" viewBox="0 0 14 18"><path d="M7 0a7 7 0 0 0-7 7c0 5 7 11 7 11s7-6 7-11a7 7 0 0 0-7-7zm0 9.5A2.5 2.5 0 1 1 7 4.5a2.5 2.5 0 0 1 0 5z" fill="#e2312a"/></svg><span>123, Lorem Ipsum is simply<br>dummy text</span></div>
  <div class="touch" style="top:150px"><svg width="16" height="16" viewBox="0 0 24 24"><path fill="#e2312a" d="M6.6 10.8a15.1 15.1 0 0 0 6.6 6.6l2.2-2.2a1 1 0 0 1 1-.25 11.4 11.4 0 0 0 3.6.57 1 1 0 0 1 1 1V20a1 1 0 0 1-1 1A17 17 0 0 1 3 4a1 1 0 0 1 1-1h3.5a1 1 0 0 1 1 1c0 1.25.2 2.45.57 3.57a1 1 0 0 1-.25 1z"/></svg><span>123 456 7890</span></div>
  <div class="touch" style="top:196px"><svg width="16" height="14" viewBox="0 0 16 12"><rect x=".5" y=".5" width="15" height="11" fill="none" stroke="#e2312a"/><path d="m.5.5 7.5 6 7.5-6" fill="none" stroke="#e2312a"/></svg><span>info@bravemotion.com</span></div>
  <div class="foot-brand"><span class="brand-dot"></span><span class="brand-name">BRAVE MOTION</span></div>
  <p class="about">Lorem Ipsum is simply dummy text of the printing and typesetting industry. Lorem Ipsum has been the industry's standard dummy text ever since the 1500s,</p>
  <div class="rule"></div>
  <p class="copy">&copy; BRAVE MOTION - 2018. All Rights Reserved.</p>
</footer>

</body>
</html>
```